International Clinical Software Company needs a new business card design

We are looking for a new business card design for our company that has recently expanded into the UK market, making us a multinational company.
After having rebranded our website and produced a new style guide, we are looking for a business card that is creative and attention grabbing, while being consistent with the style and colour scheme used on the new website, www.plumvora.example
We produce care management technology for the aged care market, but the main aspect we aim to communicate is the human element of our software, and the way it assists in providing better care for aged people, and stronger relationships between aged people and the staff that care for them.
Our current business card is a dark green with gold text, which makes the text quite difficult to read, not very aesthetically appealing and the colour scheme looks quite dated.
We would like something fresh and modern, that can still be colourful but doesn't use large blocks of dark colour, and uses the colours within our logo.
Something tying in with the leaves that are used in our logo could work quite nicely, along with the Autumn/Fall colours of soft greens, yellows and reds (also in our existing logo). However also happy to look at fresh, completely out of the box ideas we may not have yet considered.
Target Market(s)
The people that receive this business card work in the aged card or health industry and are either corporate/management level staff or clinical (Registered Nurses, care workers etc.)
Industry/Entity Type
Health Product
Contact Information for Business Card
Company Name - BrindlewayCare
Company locations: United Kingdom, Australia, New Zealand
Staff Details:
Staff name: Derek Mallow
Staff job title: Executive Chairman
Staff email: d.mallow@plumvora.example
Office phone number: 01742 918576
Font styles to use
Other font styles liked:
- Calibri
Requirements
Must have
- Must include the BrindlewayCare brand name in it's current font
- Must include logo (3 leaves in gold circle)
- Must include Business Card Details
Nice to have
- Elements of gold
- White space
- Something autumn themed but not too cliched
Should not have
- No blue - used by a major competitor and we would like to differentiate from them
- Large blocks of dark green colour (the green that appears in our leaves on the logo on our current business card is the background colour and it is far too dark)

```html
<!DOCTYPE html>
<html lang="en">
<head>
<meta charset="utf-8">
<title>BrindlewayCare Business Card</title>
<link rel="stylesheet" href="https://fonts.googleapis.com/css2?family=Carlito:wght@400;700&display=swap">
<style>
  :root {
    --page-bg: #ecebe8;
    --card-white: #ffffff;
    --gold: #b29c6e;
    --gold-text: #a8936a;
    --ink: #2b2b2b;
    --back-name: #5b4a2e;
    --leaf-orange: #e8891f;
    --leaf-yellow: #f2c53a;
    --leaf-teal: #9fd3c4;
    --leaf-light: #f1ee9c;
  }
  * { margin: 0; padding: 0; box-sizing: border-box; }
  html, body {
    width: 1200px;
    height: 900px;
    overflow: hidden;
    background: var(--page-bg);
    font-family: "Carlito", "Calibri", sans-serif;
  }
  .canvas {
    position: relative;
    width: 1200px;
    height: 900px;
  }

  /* Front card */
  .card-front {
    position: absolute;
    left: 78px;
    top: 35px;
    width: 588px;
    height: 362px;
    background: var(--card-white);
    border-radius: 14px;
    overflow: hidden;
    box-shadow: 0 4px 14px rgba(0,0,0,0.12);
  }
  .brand-band {
    position: absolute;
    left: 0;
    top: 27px;
    width: 100%;
    height: 103px;
    background: var(--gold);
  }
  .brand-circle {
    position: absolute;
    left: 229px;
    top: 13px;
    width: 144px;
    height: 144px;
    border-radius: 50%;
    background: var(--card-white);
    border: 3px solid var(--gold);
    box-shadow: 0 0 0 6px var(--card-white);
  }
  .brand-name {
    position: absolute;
    left: 0;
    top: 158px;
    width: 100%;
    text-align: center;
    font-size: 56px;
    font-weight: 400;
    color: var(--gold-text);
    line-height: 1;
  }
  .person {
    position: absolute;
    right: 339px;
    top: 255px;
    text-align: right;
  }
  .person-name {
    font-size: 22px;
    font-weight: 700;
    color: var(--gold-text);
    line-height: 1.1;
  }
  .person-title {
    font-size: 17px;
    color: var(--ink);
    margin-top: 2px;
  }
  .locations {
    position: absolute;
    left: 300px;
    top: 255px;
    font-size: 17px;
    color: var(--ink);
    line-height: 25px;
  }
  .contact {
    position: absolute;
    left: 0;
    top: 320px;
    width: 100%;
    text-align: center;
    font-size: 16px;
    color: var(--ink);
    display: flex;
    justify-content: center;
    align-items: center;
    gap: 8px;
  }
  .contact svg { width: 13px; height: 13px; }

  /* Back card */
  .card-back {
    position: absolute;
    left: 388px;
    top: 505px;
    width: 567px;
    height: 352px;
    overflow: hidden;
    box-shadow: 0 4px 14px rgba(0,0,0,0.12);
  }
  .autumn-photo {
    position: absolute;
    inset: 0;
    background:
      radial-gradient(ellipse at 62% 15%, var(--leaf-teal) 0%, rgba(159,211,196,0) 45%),
      radial-gradient(ellipse at 75% 60%, var(--leaf-light) 0%, rgba(241,238,156,0) 55%),
      radial-gradient(ellipse at 100% 30%, var(--leaf-orange) 0%, rgba(232,137,31,0) 30%),
      linear-gradient(100deg, var(--leaf-orange) 0%, var(--leaf-yellow) 35%, #e9d36a 60%, #e8ec9e 100%);
  }
  .back-name {
    position: absolute;
    right: 36px;
    bottom: 50px;
    font-size: 58px;
    font-weight: 400;
    color: var(--back-name);
    line-height: 1;
  }
</style>
</head>
<body>
<div class="canvas">

  <section class="card-front">
    <div class="brand-band"></div>
    <div class="brand-circle"></div>
    <div class="brand-name">BrindlewayCare</div>

    <div class="person">
      <div class="person-name">Derek Mallow</div>
      <div class="person-title">Executive Chairman</div>
    </div>

    <div class="locations">
      United Kingdom, Australia<br>
      New Zealand
    </div>

    <div class="contact">
      <svg viewBox="0 0 24 24" aria-hidden="true">
        <path fill="#b29c6e" d="M6.6 10.8c1.4 2.8 3.8 5.1 6.6 6.6l2.2-2.2c.3-.3.7-.4 1-.2 1.1.4 2.3.6 3.6.6.6 0 1 .4 1 1V20c0 .6-.4 1-1 1C10.6 21 3 13.4 3 4c0-.6.4-1 1-1h3.5c.6 0 1 .4 1 1 0 1.3.2 2.5.6 3.6.1.3 0 .7-.2 1L6.6 10.8z"/>
      </svg>
      <span>d.mallow@plumvora.example</span>
    </div>
  </section>

  <section class="card-back">
    <div class="autumn-photo" role="img" aria-label="Photograph of orange and yellow autumn maple leaves against a soft blurred background"></div>
    <div class="back-name">BrindlewayCare</div>
  </section>

</div>
</body>
</html>
```